TALMORK

The business want a professional looking business card. We have a scetch we will add but want the extra upgrade, and would like more suggestions for variations of our business cards.

```html
<!DOCTYPE html>
<html lang="en">
<head>
<meta charset="UTF-8">
<title>TALMORK – Business Card</title>
<link href="https://fonts.googleapis.com/css2?family=Cinzel:wght@500&family=Montserrat:wght@400;600&family=Playfair+Display:wght@700&display=swap" rel="stylesheet">
<style>
  :root {
    --page-bg: #2a2a2c;
    --card-bg: #121213;
    --gold: #d6a532;
    --gold-soft: #c99a2e;
    --ink-light: #f1f1f1;
  }
  * { box-sizing: border-box; margin: 0; padding: 0; }
  html, body {
    width: 1200px; height: 900px; overflow: hidden;
    background: var(--page-bg);
  }
  .canvas {
    width: 1200px; height: 900px;
    display: flex; flex-direction: column;
    align-items: center; justify-content: center; gap: 56px;
  }
  .card {
    position: relative;
    width: 640px; height: 366px;
    background: var(--card-bg);
    border-radius: 22px;
    box-shadow: 0 10px 30px rgba(0,0,0,0.45);
    overflow: hidden;
  }
  /* Front */
  .card--front {
    display: flex; flex-direction: column;
    align-items: center; justify-content: center;
  }
  .wordmark {
    font-family: "Cinzel", Georgia, serif;
    font-weight: 500;
    color: var(--gold);
    letter-spacing: 0.04em;
    line-height: 1;
  }
  .card--front .wordmark { font-size: 84px; }
  .tagline {
    font-family: "Montserrat", Arial, sans-serif;
    font-weight: 600;
    color: var(--gold-soft);
    letter-spacing: 0.55em;
    text-transform: uppercase;
  }
  .card--front .tagline { font-size: 17px; margin-top: 18px; margin-right: 120px; }

  /* Back */
  .card--back { padding: 36px 40px; }
  .brand-block { display: flex; flex-direction: column; align-items: flex-start; }
  .card--back .wordmark { font-size: 44px; }
  .card--back .tagline { font-size: 10px; margin-top: 8px; margin-left: 40px; letter-spacing: 0.5em; }
  .person { margin-top: 30px; }
  .person__name {
    font-family: "Playfair Display", Georgia, serif;
    font-weight: 700;
    font-size: 27px;
    color: var(--gold);
  }
  .person__role {
    font-family: "Montserrat", Arial, sans-serif;
    font-size: 14px;
    color: var(--ink-light);
    margin-top: 4px;
  }
  .contacts { list-style: none; margin-top: 26px; }
  .contacts li {
    display: flex; align-items: center; gap: 10px;
    font-family: "Montserrat", Arial, sans-serif;
    font-size: 14px; color: var(--ink-light);
    margin-bottom: 8px;
  }
  .contacts svg { width: 13px; height: 13px; flex: none; }
  .brand-emblem {
    position: absolute;
    right: 52px; top: 50%;
    width: 200px; height: 200px;
    margin-top: -60px;
    border-radius: 50%;
    background: var(--gold);
  }
</style>
</head>
<body>
<main class="canvas">
  <section class="card card--front" aria-label="Business card front">
    <h1 class="wordmark">TALMORK</h1>
    <p class="tagline">Since 2026</p>
  </section>

  <section class="card card--back" aria-label="Business card back">
    <div class="brand-block">
      <h2 class="wordmark">TALMORK</h2>
      <p class="tagline">Since 2026</p>
    </div>
    <div class="person">
      <p class="person__name">Anders Holm Lindqvist</p>
      <p class="person__role">CEO &amp; Founder</p>
    </div>
    <ul class="contacts">
      <li>
        <svg viewBox="0 0 24 24" aria-hidden="true"><path fill="#f1f1f1" d="M6.6 10.8a15.1 15.1 0 0 0 6.6 6.6l2.2-2.2a1 1 0 0 1 1-.25 11.4 11.4 0 0 0 3.6.57 1 1 0 0 1 1 1V20a1 1 0 0 1-1 1A17 17 0 0 1 3 4a1 1 0 0 1 1-1h3.5a1 1 0 0 1 1 1c0 1.25.2 2.45.57 3.6a1 1 0 0 1-.25 1z"/></svg>
        004790123456
      </li>
      <li>
        <svg viewBox="0 0 24 24" aria-hidden="true"><path fill="#f1f1f1" d="M3 5h18a1 1 0 0 1 1 1v12a1 1 0 0 1-1 1H3a1 1 0 0 1-1-1V6a1 1 0 0 1 1-1zm9 7.2L20 7H4z"/></svg>
        talmork.llc@mailbox.com
      </li>
      <li>
        <svg viewBox="0 0 24 24" aria-hidden="true"><circle cx="12" cy="12" r="9.5" fill="none" stroke="#f1f1f1" stroke-width="2"/><path d="M2.5 12h19M12 2.5c3 3 3 16 0 19M12 2.5c-3 3-3 16 0 19" fill="none" stroke="#f1f1f1" stroke-width="1.6"/></svg>
        www.talmork.llc
      </li>
    </ul>
    <div class="brand-emblem" aria-hidden="true"></div>
  </section>
</main>
</body>
</html>
```